BLS Business Card 2018

Larkmere Chiropractic. We have two locations that we want to advertise on the same card. Brightvale OrthoCore campus address: 3815 Pellham Dr., Suite 240, Flowood, MS 39417. Madison address: 246 Willowmere Dr., Building D., Madison, MS 39284. website: www.drlarkmere-example.com. o:(601)555-0147 f:(601)555-0183

Target Market(s)

Health care decision makers: primary care doctors and mothers

Contact Information for Business Card

I have no idea; up for any suggestions and I'd do much better picking from examples versus describing what I'm looking for. We are in a very high end location and would like the cards to look really sharp.

Requirements
Must have
• My name, Martin R Belvane, D.C.

```html
<!DOCTYPE html>
<html lang="en">
<head>
<meta charset="utf-8">
<title>Larkmere Chiropractic – Business Card</title>
<link href="https://fonts.googleapis.com/css2?family=Cinzel:wght@400&family=Open+Sans:wght@400;700&display=swap" rel="stylesheet">
<style>
  :root {
    --backdrop: #2b2b2c;
    --card: #0d0d0d;
    --card-edge: #1a1a1a;
    --ink: #f2f2f2;
    --ink-soft: #d6d6d6;
    --stripe: #ffffff;
    --divider: #8a8a8a;
  }
  * { box-sizing: border-box; margin: 0; padding: 0; }
  html, body { width: 1200px; height: 900px; overflow: hidden; }
  body {
    background: var(--backdrop);
    font-family: "Open Sans", Arial, sans-serif;
    color: var(--ink);
    position: relative;
  }
  .card {
    position: absolute;
    left: 320px;
    width: 560px;
    height: 320px;
    background: linear-gradient(160deg, var(--card-edge), var(--card) 60%);
    overflow: hidden;
  }
  .card--front { top: 110px; }
  .card--back { top: 470px; }
  .card__stripe {
    position: absolute;
    left: 0; right: 0;
    bottom: 12px;
    height: 9px;
    background: var(--stripe);
  }

  /* Front */
  .brand {
    position: absolute;
    top: 92px;
    left: 0; right: 0;
    display: flex;
    align-items: center;
    justify-content: center;
    gap: 16px;
  }
  .brand__mark {
    width: 40px; height: 40px;
    border: 1.5px solid var(--ink);
    border-radius: 50%;
  }
  .brand__name {
    font-family: "Cinzel", Georgia, serif;
    font-weight: 400;
    font-size: 32px;
    line-height: 1;
    letter-spacing: 1px;
    text-transform: uppercase;
    color: var(--ink);
  }
  .location {
    position: absolute;
    top: 182px;
    left: 0; right: 0;
    text-align: center;
  }
  .location__title {
    font-weight: 700;
    font-size: 13px;
    letter-spacing: 0.5px;
    text-transform: uppercase;
  }
  .location__address {
    font-size: 13px;
    color: var(--ink-soft);
    margin-top: 2px;
  }

  /* Back */
  .doctor {
    position: absolute;
    top: 92px;
    left: 40px;
    width: 230px;
    font-family: "Cinzel", Georgia, serif;
    font-size: 16px;
    letter-spacing: 0.5px;
    text-transform: uppercase;
  }
  .back__divider {
    position: absolute;
    top: 80px;
    left: 290px;
    width: 1px;
    height: 82px;
    background: var(--divider);
  }
  .contact {
    position: absolute;
    top: 84px;
    left: 310px;
    list-style: none;
  }
  .contact__item {
    display: flex;
    align-items: center;
    gap: 8px;
    font-size: 14px;
    line-height: 25px;
  }
  .contact__icon { width: 12px; height: 12px; fill: var(--ink); }
  .location--back { top: 206px; }
</style>
</head>
<body>

<section class="card card--front">
  <div class="brand">
    <span class="brand__mark"></span>
    <span class="brand__name">Larkmere Chiropractic</span>
  </div>
  <div class="location">
    <p class="location__title">Madison</p>
    <p class="location__address">246 Willowmere Dr., Building D., Madison, MS 39284.</p>
  </div>
  <div class="card__stripe"></div>
</section>

<section class="card card--back">
  <p class="doctor">Martin R Belvane, D.C.</p>
  <div class="back__divider"></div>
  <ul class="contact">
    <li class="contact__item">
      <svg class="contact__icon" viewBox="0 0 12 12" aria-hidden="true"><path d="M1 3.5C1 2 2.5 1 6 1s5 1 5 2.5V5H8.5V3.8H3.5V5H1z M2.5 6h7l1 5h-9z"/></svg>
      (601)555-0147
    </li>
    <li class="contact__item">
      <svg class="contact__icon" viewBox="0 0 12 12" aria-hidden="true"><path d="M3 1h6v3H3z M1 5h10v4H9v2H3V9H1z M4 8v2h4V8z"/></svg>
      (601)555-0183
    </li>
    <li class="contact__item">
      <svg class="contact__icon" viewBox="0 0 12 12" aria-hidden="true"><path d="M6 0.5a5.5 5.5 0 1 0 0 11a5.5 5.5 0 1 0 0-11z M3 4l2 1 1 2-1 2-2-2z M7 2l2 1-1 2-1.5-1z"/></svg>
      www.drlarkmere-example.com
    </li>
  </ul>
  <div class="location location--back">
    <p class="location__title">Brightvale OrthoCore Campus</p>
    <p class="location__address">3815 Pellham Dr., Suite 240, Flowood, MS 39417.</p>
  </div>
  <div class="card__stripe"></div>
</section>

</body>
</html>
```